VFX Company Business Card Design Project

The Kestrel Works is a decentralized Visual Effects Studio servicing the television and feature film industries.
Project Brief:
Take our logo that was previously designed on Pencil Harbor and make a double sided business card.
Requirements:
- Card MUST be double sided.
- Front of card MUST have the yellow part of our logo against the dark grey background.
- Back of card is completely up to the designer.
- Back of card must include the complete company logo.
Please follow these File Preparation guidelines:
http://printnook.ca/infopage?file=filetype_en&s=PrintNook_new&lang=en
Business

```html
<!DOCTYPE html>
<html lang="en">
<head>
<meta charset="utf-8">
<title>The Kestrel Works – Business Card</title>
<link rel="stylesheet" href="https://fonts.googleapis.com/css2?family=Jost:wght@300;400;500;600&family=PT+Sans:wght@400&display=swap">
<style>
  :root {
    --backdrop: #d2a07a;
    --card: #2b2b2b;
    --card-edge: #232323;
    --brand-yellow: #fcc72a;
    --brand-grey: #66706f;
    --tab-grey: #5f6868;
    --text-light: #f2f2ee;
    --text-soft: #d8d8d4;
    --label: #111111;
  }
  * { margin: 0; padding: 0; box-sizing: border-box; }
  html, body { width: 1200px; height: 788px; overflow: hidden; }
  body {
    background: var(--backdrop);
    font-family: "Jost", "Futura", sans-serif;
    position: relative;
  }
  .view-label {
    position: absolute;
    font-family: "PT Sans", "Myriad Pro", sans-serif;
    font-size: 22px;
    color: var(--label);
    transform: translateX(-50%);
    white-space: nowrap;
  }
  .card {
    position: absolute;
    width: 524px;
    height: 299px;
    background: var(--card);
    border-radius: 22px;
    box-shadow: 0 4px 10px rgba(0,0,0,0.35);
  }
  .card--back { left: 338px; top: 78px; }
  .card--front-mark { left: 54px; top: 446px; }
  .card--front-lockup { left: 622px; top: 446px; }

  .side-tab {
    position: absolute;
    top: 40px;
    width: 10px;
    height: 133px;
    background: var(--tab-grey);
    border-radius: 3px;
  }
  .side-tab--left { left: 0; border-radius: 0 3px 3px 0; }
  .side-tab--right { right: 0; border-radius: 3px 0 0 3px; }

  .brand-name {
    position: absolute;
    font-weight: 500;
    white-space: nowrap;
    letter-spacing: 0.5px;
  }
  .tagline {
    position: absolute;
    font-weight: 300;
    color: var(--text-soft);
    letter-spacing: 5px;
    white-space: nowrap;
  }
  .brand-dot {
    position: absolute;
    border-radius: 50%;
    background: var(--brand-yellow);
  }

  /* Back */
  .card--back .brand-name {
    left: 0; right: 0; top: 60px;
    text-align: center;
    font-size: 44px;
    color: var(--brand-grey);
  }
  .card--back .tagline {
    left: 0; right: 0; top: 126px;
    text-align: center;
    font-size: 18px;
  }
  .holder {
    position: absolute;
    left: 0; right: 0; top: 168px;
    text-align: center;
    color: var(--text-soft);
    font-size: 20px;
    font-weight: 300;
  }
  .holder .role { font-size: 14px; letter-spacing: 0.5px; }
  .contacts {
    position: absolute;
    top: 206px;
    left: 0; right: 0;
    display: flex;
    justify-content: center;
    font-size: 13px;
    line-height: 20px;
    color: var(--text-light);
  }
  .contacts dl { padding: 0 10px; }
  .contacts .col-phone { text-align: right; border-right: 1px solid #6a6a6a; }
  .contacts dt { display: inline; font-style: italic; font-weight: 600; }
  .contacts dd { display: inline; margin: 0; }
  .contacts div { white-space: nowrap; }
  .address {
    position: absolute;
    left: 0; right: 0; top: 254px;
    text-align: center;
    font-size: 13px;
    color: var(--text-light);
  }

  /* Fronts */
  .site {
    position: absolute;
    left: 0; right: 0; bottom: 18px;
    text-align: center;
    font-size: 20px;
    letter-spacing: 3px;
    color: var(--text-light);
    font-weight: 400;
  }
  .card--front-mark .brand-dot { left: 108px; top: 114px; width: 40px; height: 40px; }
  .card--front-mark .brand-name {
    left: 160px; top: 106px;
    font-size: 40px;
    color: var(--brand-yellow);
  }
  .card--front-lockup .brand-dot { left: 52px; top: 128px; width: 40px; height: 40px; }
  .card--front-lockup .brand-name {
    left: 104px; top: 122px;
    font-size: 34px;
    color: var(--brand-grey);
  }
  .card--front-lockup .tagline {
    left: 108px; top: 168px;
    font-size: 15px;
  }
</style>
</head>
<body>
  <p class="view-label" style="left:600px; top:32px;">Back</p>
  <p class="view-label" style="left:327px; top:403px;">Front - 1</p>
  <p class="view-label" style="left:900px; top:403px;">Front - 2</p>

  <section class="card card--back">
    <span class="side-tab side-tab--left"></span>
    <span class="side-tab side-tab--right"></span>
    <h1 class="brand-name">The Kestrel Works</h1>
    <p class="tagline">VIRTUAL STUDIO</p>
    <p class="holder">Your Name, <span class="role">Designation</span></p>
    <div class="contacts">
      <dl class="col-phone">
        <div><dt>cell</dt> <dd>123-456-7890</dd></div>
        <div><dt>phone</dt> <dd>123-456-7890</dd></div>
      </dl>
      <dl class="col-web">
        <div><dt>email</dt> <dd>info@website.com</dd></div>
        <div><dt>web</dt> <dd>www.website.com</dd></div>
      </dl>
    </div>
    <p class="address">0000#, Area Name, Street Name, State Name, Country code</p>
  </section>

  <section class="card card--front-mark">
    <span class="brand-dot"></span>
    <h2 class="brand-name">The Kestrel Works</h2>
    <p class="site">www.website.com</p>
  </section>

  <section class="card card--front-lockup">
    <span class="brand-dot"></span>
    <h2 class="brand-name">The Kestrel Works</h2>
    <p class="tagline">VIRTUAL STUDIO</p>
    <p class="site">www.website.com</p>
  </section>
</body>
</html>
```